Volbrey Inc Business Card

Looking to get an updated business card for a Contract Machining company (www.volbreyinc.example) - looking for a clean design the portrays the technical nature of the business - colors can follow the website design and be in any combination that makes sense (red black, white, metallic or silver) - logos attached for use also. Would like space for: Name, title, business phone (555 214-3086), cell phone , website (www.volbreyinc.example) - possibly QR code could be integrated for website (designer choice), business address - 418 Harlow Bend, Ashcombe, MI 48199 (cards will be for 4 employees, I will either need to modify a template or I can provide individual information)
Target Market(s)
Aerospace, defense and medical device manufacturing companies that need machining
Industry/Entity Type
Machining for aerospace, defense, medical
Contact Information for Business Card
Name, Title, Business Phone, Cell Phone, email, business website and business address
Look and feel

```html
<!DOCTYPE html>
<html lang="en">
<head>
<meta charset="UTF-8">
<title>Volbrey Inc Business Card</title>
<link href="https://fonts.googleapis.com/css2?family=Arimo:wght@400;700&display=swap" rel="stylesheet">
<style>
  :root {
    --brand-red: #b01f24;
    --paper: #ffffff;
    --ink: #3a3a3a;
    --muted: #8a8a8a;
    --rule: #d4d4d4;
    --stripe-gray: #6e6e6e;
    --backdrop: #3b3b3b;
  }
  * { margin: 0; padding: 0; box-sizing: border-box; }
  html, body {
    width: 1200px; height: 689px; overflow: hidden;
    background: var(--backdrop);
    font-family: "Arimo", Arial, sans-serif;
  }
  .stage {
    width: 1200px; height: 689px;
    display: flex; align-items: center; justify-content: center; gap: 50px;
  }
  .card {
    width: 525px; height: 300px;
    border-radius: 20px;
    position: relative; overflow: hidden;
  }
  /* Front */
  .card-front {
    background: var(--brand-red);
    display: flex; flex-direction: column; align-items: center; justify-content: center;
  }
  .front-mark { display: flex; flex-direction: column; align-items: center; gap: 14px; margin-bottom: 30px; }
  .front-mark .disc { width: 120px; height: 120px; border-radius: 50%; background: var(--paper); }
  .front-mark .brand-name { color: var(--paper); font-weight: 700; font-size: 24px; letter-spacing: 1px; }
  .front-url {
    position: absolute; bottom: 30px; width: 100%; text-align: center;
    color: var(--paper); font-size: 14px;
  }
  /* Back */
  .card-back { background: var(--paper); display: flex; }
  .back-brand {
    width: 44%; display: flex; flex-direction: column; align-items: center; justify-content: center; gap: 14px;
    padding-bottom: 24px;
  }
  .back-brand .disc { width: 112px; height: 112px; border-radius: 50%; background: var(--brand-red); }
  .back-brand .brand-name { color: var(--brand-red); font-weight: 700; font-size: 24px; letter-spacing: 1px; }
  .divider {
    position: absolute; left: 44%; top: 34px; bottom: 60px;
    width: 1px; background: linear-gradient(var(--rule), var(--paper));
  }
  .back-details { flex: 1; padding: 38px 0 0 24px; color: var(--ink); }
  .person-name { color: var(--brand-red); font-weight: 700; font-size: 22px; }
  .person-title { color: var(--muted); font-size: 12px; margin-top: 2px; }
  .address { font-size: 13px; line-height: 1.35; margin-top: 14px; }
  .contact-list { list-style: none; margin-top: 12px; font-size: 13px; line-height: 1.45; }
  .contact-list li { display: flex; align-items: center; gap: 8px; }
  .contact-list svg { width: 11px; height: 11px; fill: var(--brand-red); flex: none; }
  .edge-band {
    position: absolute; left: 0; right: 0; bottom: 0; height: 16px;
    background: var(--brand-red); border-top: 4px solid var(--stripe-gray);
  }
</style>
</head>
<body>
<main class="stage">
  <section class="card card-front" aria-label="Card front">
    <div class="front-mark">
      <div class="disc"></div>
      <div class="brand-name">Volbrey Inc</div>
    </div>
    <p class="front-url">www.volbreyinc.example</p>
  </section>

  <section class="card card-back" aria-label="Card back">
    <div class="back-brand">
      <div class="disc"></div>
      <div class="brand-name">VOLBREY INC</div>
    </div>
    <div class="divider"></div>
    <div class="back-details">
      <h1 class="person-name">Dana Whitlow</h1>
      <p class="person-title">President</p>
      <p class="address">418 Harlow Bend<br>Ashcombe, MI 48199</p>
      <ul class="contact-list">
        <li><svg viewBox="0 0 24 24"><path d="M6.6 10.8a15 15 0 0 0 6.6 6.6l2.2-2.2a1 1 0 0 1 1-.25 11.4 11.4 0 0 0 3.6.57 1 1 0 0 1 1 1V20a1 1 0 0 1-1 1A17 17 0 0 1 3 4a1 1 0 0 1 1-1h3.5a1 1 0 0 1 1 1c0 1.250.2 2.450.57 3.57a1 1 0 0 1-.25 1z"/></svg>555 214-3086</li>
        <li><svg viewBox="0 0 24 24"><path d="M7 1h10a2 2 0 0 1 2 2v18a2 2 0 0 1-2 2H7a2 2 0 0 1-2-2V3a2 2 0 0 1 2-2zm0 3v14h10V4z"/></svg>555 803-7721</li>
        <li><svg viewBox="0 0 24 24"><path d="M2 5h20v14H2zm2 2v.5l8 5 8-5V7z"/></svg>info@volbreyinc.example</li>
        <li><svg viewBox="0 0 24 24"><circle cx="12" cy="12" r="10"/></svg>www.volbreyinc.example</li>
      </ul>
    </div>
    <div class="edge-band"></div>
  </section>
</main>
</body>
</html>
```